Verodex business card

Business card for sustainable investment company called "Verodex". Verodex is an exchange platform selling carbon credits between buyers and sellers. Carbon Credits are an environmental commodity for reducing global carbon emissions.

the card should obviously have our logo and the theme should be sustainability/environment mixed with a trading platform.

Contact Information for Business Card

Logo, Name, Title, Phone, Email

Colors
0054AA
0677BA
7BADD7
CADEEF
E8F1F8
0094D4
00A9DD
6FCCEA
C7EBF8
E9F6FB
00AB8E
00BBA5
67D7C9
C6EFE9
E9F9F6
59FF00
82FF00
B8FF75
E3FFCB
F4FFEA

```html
<!DOCTYPE html>
<html lang="en">
<head>
<meta charset="utf-8">
<title>Verodex Business Card</title>
<link rel="stylesheet" href="https://fonts.googleapis.com/css2?family=Montserrat:wght@400;500;700&display=swap">
<style>
  :root {
    --navy: #172a52;
    --blue: #4a80c8;
    --icon: #4a9ad0;
    --ink: #1c1f2a;
    --pale: #eef5fa;
    --white: #ffffff;
    --backdrop: #3a3a3c;
  }
  * { margin: 0; padding: 0; box-sizing: border-box; }
  html, body {
    width: 1200px; height: 1059px; overflow: hidden;
    background: var(--backdrop);
    font-family: "Montserrat", sans-serif;
  }
  .card { position: absolute; overflow: hidden; }
  .card-front { left: 256px; top: 100px; width: 688px; height: 391px; background: var(--white); }
  .card-back { left: 253px; top: 537px; width: 694px; height: 394px; background: var(--navy); }

  .front-accent {
    position: absolute; left: 444px; top: -150px;
    width: 430px; height: 430px; border-radius: 50%;
    background: var(--pale);
  }
  .brand { position: absolute; display: flex; align-items: center; }
  .brand-square { background: var(--blue); border-radius: 6px; }
  .brand-name { font-weight: 700; letter-spacing: 0.5px; line-height: 1; }
  .card-front .brand { left: 29px; top: 78px; }
  .card-front .brand-square { width: 56px; height: 56px; margin-right: 22px; }
  .card-front .brand-name { font-size: 53px; color: var(--navy); }

  .name-bar { position: absolute; left: 0; top: 214px; width: 16px; height: 41px; background: var(--blue); }
  .person-name { position: absolute; left: 30px; top: 208px; font-size: 28px; font-weight: 700; color: var(--blue); letter-spacing: 0.6px; }
  .person-title { position: absolute; left: 30px; top: 239px; font-size: 17px; font-weight: 400; color: var(--ink); letter-spacing: 0.5px; }

  .contact-list { position: absolute; left: 29px; top: 293px; list-style: none; }
  .contact-list li { display: flex; align-items: center; height: 26.5px; font-size: 16px; color: var(--ink); letter-spacing: 0.3px; }
  .contact-list svg { width: 13px; height: 13px; margin-right: 7px; fill: var(--icon); }

  .divider { position: absolute; left: 311px; top: 328px; width: 1px; height: 35px; background: var(--ink); }
  .address { position: absolute; left: 328px; top: 323px; font-size: 16px; line-height: 22.5px; color: var(--ink); letter-spacing: 0.3px; }

  .card-back .brand { left: 50%; top: 50%; transform: translate(-50%, -50%); }
  .card-back .brand-square { width: 70px; height: 70px; margin-right: 24px; }
  .card-back .brand-name { font-size: 66px; color: var(--white); }
</style>
</head>
<body>
  <section class="card card-front">
    <div class="front-accent"></div>
    <div class="brand">
      <span class="brand-square"></span>
      <span class="brand-name">VERODEX</span>
    </div>
    <div class="name-bar"></div>
    <h1 class="person-name">DARYL BROOKS</h1>
    <p class="person-title">MANAGER</p>
    <ul class="contact-list">
      <li>
        <svg viewBox="0 0 24 24"><path d="M6.6 10.8a15.2 15.2 0 0 0 6.6 6.6l2.2-2.2a1 1 0 0 1 1-.25 11.4 11.4 0 0 0 3.6.57 1 1 0 0 1 1 1V20a1 1 0 0 1-1 1A17 17 0 0 1 3 4a1 1 0 0 1 1-1h3.5a1 1 0 0 1 1 1c0 1.25.2 2.45.57 3.57a1 1 0 0 1-.25 1z"/></svg>
        123-456-7890
      </li>
      <li>
        <svg viewBox="0 0 24 24"><path d="M2 5h20v2l-10 6L2 7z"/><path d="M2 9l10 6 10-6v10H2z"/></svg>
        info@youremail.com
      </li>
      <li>
        <svg viewBox="0 0 24 24"><path d="M12 2a10 10 0 1 0 0 20 10 10 0 0 0 0-20zm6.9 6h-2.9a15 15 0 0 0-1.4-3.6A8 8 0 0 1 18.9 8zM12 4a13 13 0 0 1 1.9 4h-3.8A13 13 0 0 1 12 4zM4.3 14a8 8 0 0 1 0-4h3.4a16 16 0 0 0 0 4zm.8 2h2.9a15 15 0 0 0 1.4 3.6A8 8 0 0 1 5.1 16zM8 8H5.1a8 8 0 0 1 4.3-3.6A15 15 0 0 0 8 8zm4 12a13 13 0 0 1-1.9-4h3.8A13 13 0 0 1 12 20zm2.3-6H9.7a14 14 0 0 1 0-4h4.6a14 14 0 0 1 0 4zm.3 5.6a15 15 0 0 0 1.4-3.6h2.9a8 8 0 0 1-4.3 3.6zm1.7-5.6a16 16 0 0 0 0-4h3.4a8 8 0 0 1 0 4z"/></svg>
        www.yourwebsite.com
      </li>
    </ul>
    <div class="divider"></div>
    <p class="address">2217 Harbor Field Rd. Westbrook<br>Lane Ashford, MN 02840</p>
  </section>

  <section class="card card-back">
    <div class="brand">
      <span class="brand-square"></span>
      <span class="brand-name">VERODEX</span>
    </div>
  </section>
</body>
</html>
```